Cosmetic oil label design

We need a label for a cosmetic oganic Argan Oil. The oil is organic imported from Morocco, cold pressed without any preservatives. The lable is for our round 30ml Airless Bottle with clear body Matte Gold Cap, Shiny Gold Collar. We want to communicate that our product is organic natural and works for all beauty needs. We want the emphasis on the words No preservatives, additives or perfumes
We have attached a picture of the bottle and our compnay's logo.

the bottle demensions are Width/Front: 33.0mm
Length/Depth: 33.0mm
Height: 115.0mm
Lable demensions: Lenght 4inch, width 1.75inch.

let us know if you need any other information, cheers!
Updates

Target Market(s)

Our target customer is mainly women 16-70, and also men or anyone looking to have healthy skin and hair using natural products

Industry/Entity Type

Product

Requirements
Must have
• Front side must have:
- attached logo
-words: Authentic Moroccan Argan Oil, No preservatives, additives or perfumes,
L’Huile d’Argan, Produit du Maroc, Imported from Morocco, 30ml

Back side
-Ingredients: 100% Pure Argania Spinosa (Argan Oil)
-Directions: Message into skin, hair or desired area until completely absorbed
-Manufactured for and distributed by Velora Traders
482 W 97th street New York , NY 10027
Nice to have
• Would be nice if we can fit the following information in the back of the label

Rich in vitamin E and essential fatty acids,Argan oil has several benefits. It Hydrates and nourishes skin and hair. Can be used for treating dry skin, split ends softening cuticles. It works for all types of skin.

```html
<!DOCTYPE html>
<html lang="en">
<head>
<meta charset="utf-8">
<title>Argan Oil Back Label</title>
<link rel="stylesheet" href="https://fonts.googleapis.com/css2?family=PT+Sans:wght@400;700&display=swap">
<style>
  :root {
    --brown-deep: #24170f;
    --brown-oval: #2a1c13;
    --gold-glow: #f1c66a;
    --gold-mid: #c99a45;
    --gold-light: #f2cb78;
    --gold-text: #e8b65e;
    --ink: #2a1c13;
  }
  html, body {
    margin: 0;
    padding: 0;
    width: 1200px;
    height: 2740px;
    overflow: hidden;
    background: var(--brown-deep);
  }
  .label {
    position: relative;
    width: 1200px;
    height: 2740px;
    overflow: hidden;
    font-family: "PT Sans", sans-serif;
    background:
      radial-gradient(ellipse 600px 980px at 610px 800px, var(--gold-glow) 0%, #d6a24a 50%, rgba(120,80,30,0.55) 72%, rgba(36,23,15,0) 92%),
      linear-gradient(180deg, var(--brown-deep) 0%, #5a3c1c 35%, var(--gold-mid) 58%, var(--gold-light) 95%);
  }
  .benefits-oval {
    position: absolute;
    left: 0;
    top: 0;
  }
  .ornament {
    position: absolute;
    top: 1180px;
    width: 96px;
    height: 80px;
    border-radius: 50%;
    background: var(--brown-oval);
  }
  .ornament--left { left: 86px; }
  .ornament--right { right: 86px; }
  .benefits-text {
    position: absolute;
    left: 110px;
    width: 1000px;
    top: 4px;
    margin: 0;
    text-align: center;
    color: var(--gold-text);
    font-size: 78px;
    line-height: 104px;
  }
  .back-info {
    position: absolute;
    left: 0;
    width: 1200px;
    text-align: center;
    color: var(--ink);
    margin: 0;
  }
  .back-info h2 {
    margin: 0;
    font-weight: 400;
    font-size: 76px;
    line-height: 78px;
  }
  .back-info p {
    margin: 0;
    font-size: 76px;
    line-height: 80px;
  }
  .ingredients { top: 1661px; }
  .directions { top: 1949px; }
  .directions p { line-height: 86px; }
  .manufacturer {
    position: absolute;
    top: 2337px;
    left: 0;
    width: 1200px;
    margin: 0;
    text-align: center;
    color: var(--ink);
    font-size: 58px;
    line-height: 70px;
  }
  .origin-band {
    position: absolute;
    left: 0;
    bottom: 0;
    width: 1200px;
    height: 132px;
    background: var(--brown-deep);
    color: var(--gold-text);
    font-size: 86px;
    letter-spacing: 6px;
    line-height: 132px;
    text-align: center;
  }
</style>
</head>
<body>
<main class="label">
  <svg class="benefits-oval" width="1200" height="1600" viewBox="0 0 1200 1600" aria-hidden="true">
    <ellipse cx="610" cy="798" rx="390" ry="790" fill="var(--brown-oval)"/>
  </svg>
  <div class="ornament ornament--left" role="img" aria-label="Decorative leaf flourish"></div>
  <div class="ornament ornament--right" role="img" aria-label="Decorative leaf flourish"></div>

  <p class="benefits-text">
    Rich in<br>
    vitamin E<br>
    and essential<br>
    fatty acids,<br>
    Argan oil has<br>
    several benefits.<br>
    It hydrates &amp; nourishes<br>
    skin &amp; hair. Can<br>
    be used for treating<br>
    dry skin, dry hair,<br>
    split ends soften<br>
    cuticles. It works for<br>
    all types<br>
    of skin
  </p>

  <section class="back-info ingredients">
    <h2>Ingredients</h2>
    <p>100% Pure Argania Spinosa<br>(Argan Oil)</p>
  </section>

  <section class="back-info directions">
    <h2>Directions</h2>
    <p>Massage into skin,<br>hair or desired area until<br>completely absorbed.</p>
  </section>

  <p class="manufacturer">
    Manufactured for and distributed<br>
    by Velora Traders 482 W 97th<br>
    street New York , NY 10027
  </p>

  <footer class="origin-band">Imported from Morocco.</footer>
</main>
</body>
</html>
```